Dietitian needs awesome business card

I need a contemporary design that's eye catching but professional.
My card is to given to doctors, specialists and patients alike.
I manage patients with chronic diseases
I have uploaded my logo and current business card, I would also like the other Certified Clinical Nutritionist logo incorporated into the design

Target Market(s)

Doctors, specialists and patients

Industry/Entity Type

Healthcare

Contact Information for Business Card

www.brightfieldnutrition.com.au
Ph: 0427 561 903
Fax: 6457 2183
email: marcus.k.diet@fernmail.com
Space on the back of the card with: Appointment date, Appointment time and appointment location

Font styles to use
Serif

Colors
fbee3e
876aae
ffc214

Requirements
Must have
• My Logo
• Certified Clinical Nutritionist Logo
• My 4 locations - Pinebrook Medical Centre, North Corrin Health, Hollis Medical, Ashcombe Doctors Surgery
Nice to have
• I like the colours in my current business card

```html
<!DOCTYPE html>
<html lang="en">
<head>
<meta charset="utf-8">
<title>Brightfield Nutrition &amp; Dietetics – Business Card</title>
<link rel="stylesheet" href="https://fonts.googleapis.com/css2?family=Cabin:ital,wght@0,400;0,500;0,700;1,700&display=swap">
<style>
  :root {
    --backdrop: #e9e6e3;
    --card: #ffffff;
    --band-light: #1a8ad6;
    --band-dark: #1d4fae;
    --navy: #1b2c8c;
    --green: #7ac143;
    --rule: #7d86c4;
  }
  * { box-sizing: border-box; margin: 0; padding: 0; }
  html, body {
    width: 1200px; height: 900px; overflow: hidden;
    background: var(--backdrop);
    font-family: "Cabin", sans-serif;
  }
  .canvas { position: relative; width: 1200px; height: 900px; }

  .card {
    position: absolute;
    background: var(--card);
    border-radius: 16px;
    box-shadow: 0 6px 18px rgba(0,0,0,.12);
    overflow: hidden;
  }
  .card--front { left: 78px; top: 35px; width: 588px; height: 363px; }
  .card--back  { left: 389px; top: 507px; width: 565px; height: 348px; }

  .band {
    position: absolute; left: 0; right: 0;
    background: linear-gradient(to bottom, var(--band-light), var(--band-dark));
  }
  .card--front .band { top: 92px; height: 86px; }
  .card--back .band  { top: 38px; height: 85px; }

  .brand-disc {
    position: absolute;
    border-radius: 50%;
    background: var(--card);
  }
  .card--front .brand-disc { left: 227px; top: 66px; width: 136px; height: 136px; }
  .card--back .brand-disc  { left: 219px; top: 8px; width: 128px; height: 128px; }

  .holder-name {
    position: absolute; top: 27px; left: 0; width: 590px;
    text-align: center;
    color: var(--green);
    font-weight: 700; font-size: 19px; letter-spacing: .3px;
    text-transform: uppercase;
  }

  .wordmark {
    position: absolute; left: 0; right: 0;
    text-align: center;
    color: var(--navy);
    font-weight: 500;
    line-height: 1;
  }
  .wordmark__main { display: block; font-size: 44px; }
  .wordmark__sub  { display: block; font-size: 21px; margin-top: 6px; }
  .card--front .wordmark { top: 200px; left: -6px; }
  .card--back .wordmark  { top: 145px; left: 0; }

  .contact {
    position: absolute; top: 293px; left: 0; width: 590px;
    text-align: center;
    color: var(--navy);
    font-size: 15.5px; line-height: 21px;
  }
  .contact .sep { margin: 0 5px; }

  .appointment {
    position: absolute; top: 256px; left: 84px;
    display: flex; gap: 6px; align-items: baseline;
    color: var(--green); font-weight: 700; font-size: 15px;
  }
  .appointment .field { display: flex; align-items: baseline; gap: 4px; }
  .appointment .blank {
    display: inline-block; width: 78px; height: 1px;
    border-bottom: 1px solid var(--rule);
    margin-right: 4px;
  }
  .notice {
    position: absolute; top: 303px; left: 0; right: 0;
    text-align: center; padding-left: 14px;
    color: var(--navy);
    font-style: italic; font-weight: 700; font-size: 15px;
  }
</style>
</head>
<body>
<main class="canvas">

  <section class="card card--front" aria-label="Card front">
    <p class="holder-name">Marcus Kellaway</p>
    <div class="band"></div>
    <div class="brand-disc"></div>
    <h1 class="wordmark">
      <span class="wordmark__main">Brightfield</span>
      <span class="wordmark__sub">Nutrition &amp; Dietetics</span>
    </h1>
    <address class="contact" style="font-style:normal">
      0427 561 903<span class="sep">|</span>6457 2183<span class="sep">|</span>marcus.k.diet@fernmail.com<br>
      www.brightfieldnutrition.com.au
    </address>
  </section>

  <section class="card card--back" aria-label="Card back">
    <div class="band"></div>
    <div class="brand-disc"></div>
    <h2 class="wordmark">
      <span class="wordmark__main">Brightfield</span>
      <span class="wordmark__sub">Nutrition &amp; Dietetics</span>
    </h2>
    <div class="appointment">
      <span class="field">Date: <span class="blank"></span></span>
      <span class="field">Time: <span class="blank"></span></span>
      <span class="field">Location: <span class="blank"></span></span>
    </div>
    <p class="notice">If unable to keep appointment, kindly give 24hrs notice.</p>
  </section>

</main>
</body>
</html>
```